Business cards for Zestcycle

We need a business card layout for our new bike and e-bike rental (we also sell used e-bikes and bike accessories). The logo already exists.

```html
<!DOCTYPE html>
<html lang="en">
<head>
<meta charset="utf-8">
<title>Zestcycle – Business Cards</title>
<link href="https://fonts.googleapis.com/css2?family=Open+Sans:wght@400;700&family=Cabin:wght@500&family=Roboto:wght@400&display=swap" rel="stylesheet">
<style>
  :root {
    --stage: #e3e3e3;
    --paper: #ffffff;
    --teal: #52bf9f;
    --ink: #1b2b33;
    --ink-soft: #3b464c;
    --night: #1d333b;
    --night-pattern: #213b43;
    --rule: #c9c9c9;
    --white: #ffffff;
  }
  * { box-sizing: border-box; margin: 0; padding: 0; }
  html, body { width: 1200px; height: 802px; overflow: hidden; }
  body { background: var(--stage); position: relative; }

  .card {
    position: absolute;
    top: 274px;
    width: 443px;
    height: 265px;
    box-shadow: 0 3px 8px rgba(0,0,0,0.25);
  }
  .card--front { left: 136px; background: var(--paper); }
  .card--back { left: 624px; background: var(--night); overflow: hidden; }

  /* Front: brand block */
  .brand {
    position: absolute;
    left: 0; width: 227px;
    top: 122px;
    display: flex;
    flex-direction: column;
    align-items: center;
  }
  .brand__name {
    display: flex;
    align-items: center;
    gap: 7px;
    font-family: "Open Sans", sans-serif;
    font-weight: 700;
    font-size: 30px;
    line-height: 1;
    color: var(--ink);
  }
  .brand__dot {
    width: 11px; height: 11px;
    border-radius: 50%;
    background: var(--teal);
    flex: none;
  }
  .brand__tagline {
    margin-top: 22px;
    font-family: "Cabin", sans-serif;
    font-weight: 500;
    font-size: 12.5px;
    color: var(--ink);
  }
  .divider {
    position: absolute;
    left: 227px; top: 58px;
    width: 1px; height: 140px;
    background: var(--rule);
  }

  /* Front: contact block */
  .contact {
    position: absolute;
    left: 245px; top: 63px;
    color: var(--ink-soft);
    font-family: "Roboto", Arial, sans-serif;
  }
  .contact__name {
    font-family: "Open Sans", sans-serif;
    font-weight: 700;
    font-size: 15.5px;
    line-height: 18px;
    color: var(--ink);
    letter-spacing: 0.2px;
  }
  .contact__name span { color: var(--teal); }
  .contact__role { font-size: 12.5px; line-height: 15px; margin-bottom: 7px; }
  .contact__list { list-style: none; }
  .contact__list li {
    display: flex; align-items: center; gap: 4px;
    font-size: 12.5px; line-height: 16px;
  }
  .contact__list svg { width: 9px; height: 9px; fill: var(--ink); flex: none; }
  .contact__address { margin-top: 3px; font-size: 12.8px; line-height: 15.5px; }

  /* Back */
  .back__pattern {
    position: absolute; inset: 0;
    background: linear-gradient(var(--night), var(--night-pattern) 50%, var(--night));
  }
  .back__name {
    position: absolute; inset: 0;
    display: flex; align-items: center; justify-content: center;
    gap: 10px;
    font-family: "Open Sans", sans-serif;
    font-weight: 700;
    font-size: 38px;
    color: var(--white);
  }
  .back__name .brand__dot { width: 14px; height: 14px; }
</style>
</head>
<body>

<section class="card card--front" aria-label="Business card front">
  <div class="brand">
    <div class="brand__name"><span class="brand__dot"></span>Zestcycle</div>
    <div class="brand__tagline">leicht unterwegs</div>
  </div>
  <div class="divider"></div>
  <div class="contact">
    <div class="contact__name">MARTEN <span>KOVAC</span></div>
    <div class="contact__role">Managing Director</div>
    <ul class="contact__list">
      <li><svg viewBox="0 0 10 10"><path d="M1 3 Q5 0 9 3 L8 4.5 L6.5 4 L6.5 3.3 Q5 2.8 3.5 3.3 L3.5 4 L2 4.5 Z M2.5 5 H7.5 L8.5 9 H1.5 Z"/></svg>031-482 907 215</li>
      <li><svg viewBox="0 0 10 10"><path d="M2.5 0 H7.5 V10 H2.5 Z M3.5 1.2 V7.8 H6.5 V1.2 Z"/></svg>031-482 907 215</li>
      <li><svg viewBox="0 0 10 10"><path d="M0 2 H10 V8 H0 Z M0.8 2.6 L5 5.6 L9.2 2.6 Z"/></svg>hello@zestcycle.de</li>
      <li><svg viewBox="0 0 10 10"><circle cx="5" cy="5" r="4.6"/></svg>www.zestcycle.de</li>
    </ul>
    <div class="contact__address">48213, Lindenweg 14<br>Germany, Münster.</div>
  </div>
</section>

<section class="card card--back" aria-label="Business card back">
  <div class="back__pattern" role="img" aria-label="Faint repeating bicycle pattern across the dark background"></div>
  <div class="back__name"><span class="brand__dot"></span>Zestcycle</div>
</section>

</body>
</html>
```